Create an awesome website for a medical clinic

This is a new website for a doctor's office. The site should be clean and modern, easy to navigate.

This is a wellness clinic, we want to help our clients have a healthy, active lifestyle. It should be friendly and inviting, and easy for them to call or schedule an appointment.

The site should be responsive and designed using the attached Bootstrap 3 PSD.

We will provide stock photos, until then please use stock photos from:

pixelharbor.com or
framequarry.com (preferred)

Some example sites of clean and modern designs that we like:

https://tulsaspinecare.com/
http://reachpastjoints.com/
http://turninghealthier.com/

Also attached is a temporary logo you can use.

Reason: Thank you everyone for your great designs - we need a little more time so I'm extending the project.

Need extra days to review

Also, the colors in the new logo I just linked to are the final colors of the logo, so feel free to use any complimentary colors to it.

Hi everyone, The boss wants to change the layout of the site a little bit - here's the revised layout: https://www.filecrate.com/s/k9rt31vx2qp84zn/notes%2011_29_2017.pdf?dl=0 And the graphic assets you can use are here: https://www.filecrate.com/s/k9rt31vx2qp84zn/notes%2011_29_2017.pdf?dl=0 Feel free to change the background color of the "topbar", and change the icons of the "why people trust us" if you want, these are just temporary placeholders. Thanks for your patience and hard work!

Target Market(s)

People seeking medical treatment (wellness clinic)

Industry/Entity Type

Doctor

Number of Pages Required

1 page

Font styles to use
Sans Serif

Colors
0592cd
33a6d7
abd037
9bcb3c

Requirements
Must have
• The home page should have: a strong hero image/slideshow, clinic phone number should be prominent and at the top of the page (in the nav), a "what to expect" section (this is like a FAQs section - see attachment), and a strong call to action (a button to call or schedule an appointment).
• The what to expect section is useful so that prospective clients can determine if we're a good fit for them or not. It's a basic, first-step pre-qualification block of information.
• Social media icons which links to our social media profiles should be included.
Nice to have
• - Link to 3 most recent blog entries
• - Testimonials
• - How a multilevel nav menu looks.

```html
<!DOCTYPE html>
<html lang="en">
<head>
<meta charset="utf-8">
<title>Meadow Medical Clinic</title>
<link href="https://fonts.googleapis.com/css2?family=Open+Sans:wght@400;600;700&family=Roboto+Condensed:wght@400;700&family=Oswald:wght@400;500&display=swap" rel="stylesheet">
<style>
:root{
  --green:#2aa74a;
  --green-dark:#1f9a3f;
  --lime:#9bcb3c;
  --blue:#0592cd;
  --blue-light:#33a6d7;
  --ink:#222;
  --text:#555;
  --muted:#8a8a8a;
  --grey-bg:#f1f1f1;
  --footer:#1f1f1f;
  --footer-text:#d8d8d8;
  --white:#fff;
}
*{margin:0;padding:0;box-sizing:border-box}
html,body{width:1200px;height:3789px;overflow:hidden}
body{position:relative;font-family:"Open Sans",Arial,sans-serif;color:var(--text);background:var(--white)}
.abs{position:absolute}
.heading{font-family:"Roboto Condensed",Arial,sans-serif;font-weight:400;color:var(--ink);text-transform:uppercase;font-size:30px;letter-spacing:.3px}
.btn{display:inline-block;background:var(--green);color:var(--white);border-radius:16px;font-size:12px;padding:8px 18px;font-weight:600}
p{font-size:13px;line-height:23px}

/* header */
.site-header{left:0;top:0;width:1200px;height:121px;background:var(--white)}
.brand{display:flex;align-items:center;gap:12px;font-family:"Open Sans",Arial,sans-serif;font-weight:700;font-size:26px;line-height:1;white-space:nowrap}
.brand .dot{width:18px;height:18px;border-radius:50%;flex:none}
.brand-top{left:90px;top:44px;color:var(--green)}
.brand-top .dot{background:var(--green)}
.phone{left:692px;top:40px;display:flex;gap:14px;align-items:center}
.phone .lbl{font-size:15px;color:#444;line-height:19px}
.cta{left:895px;top:44px;width:216px;height:36px;border-radius:18px;background:var(--blue);color:var(--white);font-size:13px;text-align:center;line-height:36px}

.main-nav{left:0;top:121px;width:1200px;height:61px;background:linear-gradient(#9bcb3c,#7fba2e)}
.main-nav ul{list-style:none;display:flex;height:61px;padding-left:91px}
.main-nav li{color:var(--white);font-size:16px;line-height:61px;padding:0 31px}
.main-nav li.active{background:var(--green-dark)}

.hero{left:0;top:182px;width:1200px;height:505px;background:linear-gradient(160deg,#7dbf3a 0%,#4f9a2a 45%,#8cc54a 100%)}
.hero-title{left:577px;top:405px;font-family:"Oswald",Arial,sans-serif;font-weight:500;color:var(--white);font-size:50px;line-height:56px}
.hero-sub{left:588px;top:466px;font-family:"Open Sans",Arial,sans-serif;color:var(--white);font-size:34px}

/* welcome */
.welcome h2{left:107px;top:790px}
.welcome p{left:107px;top:838px;width:484px;text-align:justify;font-size:12.5px;line-height:22px}
.welcome .btn{left:107px;top:985px}
.video{left:630px;top:773px;width:462px;height:270px;border:1px solid #ddd;padding:5px;background:var(--white)}
.video .shot{width:100%;height:100%;background:linear-gradient(135deg,#dfe8ef,#9fb4c4 60%,#6f8796)}
.play{left:826px;top:880px}

/* services */
.services{left:0;top:1124px;width:1200px;height:493px;background:linear-gradient(90deg,#0b8fd0,#1a9bd8 50%,#0a8bcc)}
.svc{top:1296px;width:320px;text-align:center;color:var(--white)}
.svc .ring{width:110px;height:110px;margin:0 auto;border:2px solid rgba(255,255,255,.85);border-radius:50%;display:flex;align-items:center;justify-content:center}
.svc h3{font-weight:400;font-size:20px;margin-top:18px}
.svc p{font-size:12px;line-height:21px;margin-top:8px;padding:0 40px}
.svc .more{font-size:12px;margin-top:12px}

/* what we do */
.whatwedo{left:0;top:1617px;width:1200px;height:442px;background:var(--grey-bg)}
.portrait{left:137px;top:1700px;width:294px;height:294px;border-radius:50%;border:3px solid #cfe7c8;padding:6px;background:var(--white)}
.portrait div{width:100%;height:100%;border-radius:50%;background:radial-gradient(circle at 50% 40%,#f4f6f7,#c9d6de)}

/* expect */
.expect h2{left:0;top:2140px;width:1200px;text-align:center}
.faq{top:2223px;width:329px;height:177px;background:var(--white);box-shadow:0 2px 6px rgba(0,0,0,.15)}
.faq .q{height:43px;background:var(--blue);color:var(--white);font-size:12.5px;padding:0 12px;display:flex;justify-content:space-between;align-items:center}
.faq .a{padding:24px 16px;font-size:12.5px;line-height:24px;color:#444}

/* testimonial */
.testimonial{left:0;top:2513px;width:1200px;height:422px;background:linear-gradient(90deg,#1f9e45,#27ab4b 50%,#1e9a42)}
.quote{left:240px;top:2645px;width:720px;text-align:center;color:var(--white);font-size:13.5px;line-height:23px}
.avatar{left:550px;top:2736px;width:97px;height:97px;border-radius:50%;border:3px solid var(--white);background:linear-gradient(#e9e4df,#b9aba0)}
.person{left:0;top:2850px;width:1200px;text-align:center;color:var(--white);font-size:11px;font-style:italic}

/* blog */
.blog h2{left:0;top:3027px;width:1200px;text-align:center}
.post{top:3107px;width:313px;height:308px;background:var(--white);box-shadow:0 2px 6px rgba(0,0,0,.15);text-align:center}
.post .img{height:167px;position:relative}
.post .date{position:absolute;left:78px;bottom:-12px;width:158px;height:24px;background:var(--blue-light);color:var(--white);font-size:11px;line-height:24px}
.post h4{font-weight:400;color:#333;font-size:14px;margin-top:34px;letter-spacing:.4px}
.post p{font-size:11px;line-height:17px;color:var(--muted);padding:8px 28px 0}
.post .more{font-size:11px;color:var(--blue);margin-top:6px}

/* footer */
.site-footer{left:0;top:3486px;width:1200px;height:303px;background:var(--footer)}
.brand-foot{left:113px;top:3590px;color:var(--green);font-size:24px}
.brand-foot .dot{background:var(--green)}
.fcol{color:var(--footer-text)}
.fcol h5{font-weight:400;font-size:12px;color:var(--white);letter-spacing:.4px}
.contact-list{list-style:none;margin-top:20px;font-size:11px;line-height:17px}
.contact-list li{display:flex;gap:10px;margin-bottom:10px;align-items:flex-start}
.contact-list svg{margin-top:2px;flex:none}
.fcol .note{font-size:11px;line-height:16px;margin-top:18px;width:150px}
.mail-form{display:flex;margin-top:12px}
.mail-form .field{width:145px;height:28px;background:var(--white);color:#999;font-size:11px;padding:7px 8px}
.mail-form .go{height:28px;background:var(--green);color:var(--white);font-size:11px;padding:7px 8px}
.social{display:flex;gap:10px;margin-top:22px}
.social span{width:22px;height:22px;background:#e6e6e6;border-radius:3px}
.divider{left:0;top:3688px;width:1200px;height:1px;background:#3a3a3a}
.copy{left:0;top:3705px;width:1200px;text-align:center;font-size:11px;color:#ccc}
</style>
</head>
<body>

<header class="site-header abs">
  <div class="brand brand-top abs"><span class="dot"></span><span>Meadow Medical Clinic</span></div>
  <div class="phone abs">
    <svg width="20" height="34" viewBox="0 0 20 34"><rect x="1" y="1" width="18" height="32" rx="3" fill="none" stroke="#2aa74a" stroke-width="2.5"/><rect x="4" y="5" width="12" height="20" fill="#2aa74a"/><circle cx="10" cy="29" r="1.8" fill="#2aa74a"/></svg>
    <div class="lbl">Phone<br>(555) 410-2286</div>
  </div>
  <div class="cta abs">Schedule an Appointment</div>
</header>

<nav class="main-nav abs">
  <ul>
    <li class="active">Home</li><li>About us</li><li>Service</li><li>Treatment</li><li>Testimonials</li><li>Blog</li><li>Contacts</li>
  </ul>
</nav>

<section class="hero abs" role="img" aria-label="Photo of a joyful woman with raised arms in a sunny green meadow"></section>
<div class="hero-title abs">MEADOW MEDICAL CLINIC</div>
<div class="hero-sub abs">This is a wellness clinic</div>

<section class="welcome">
  <h2 class="heading abs">Welcome to Meadow</h2>
  <p class="abs">It is a long established fact that a reader will be distracted by the readable content of a page when looking at its layout. The point of using Lorem Ipsum is that it has a more-or-less normal distribution of letters, as opposed to using 'Content here, content here', making it look like readable English. Many desktop publishing packages and web page editors now use Lorem Ipsum as their default model text.</p>
  <span class="btn abs">Read More</span>
  <div class="video abs"><div class="shot" role="img" aria-label="Video still of a doctor consulting a patient in a bright office"></div></div>
  <svg class="play abs" width="60" height="60" viewBox="0 0 60 60"><circle cx="30" cy="30" r="28" fill="rgba(40,40,40,.55)" stroke="#fff" stroke-width="2"/><path d="M24 18 L42 30 L24 42 Z" fill="#fff"/></svg>
</section>

<section class="services abs" role="img" aria-label="Soft blue-tinted background photo of an active cyclist"></section>
<h2 class="heading abs" style="left:0;top:1204px;width:1200px;text-align:center;color:#fff">Our Services</h2>
<div class="svc abs" style="left:114px">
  <div class="ring"><svg width="44" height="40" viewBox="0 0 44 40" fill="#fff"><circle cx="22" cy="10" r="7"/><circle cx="9" cy="14" r="5"/><circle cx="35" cy="14" r="5"/><path d="M10 38c0-9 5-16 12-16s12 7 12 16z"/><path d="M0 34c0-7 4-12 9-12 2 0 3 1 4 2-3 3-4 6-4 10z"/><path d="M44 34c0-7-4-12-9-12-2 0-3 1-4 2 3 3 4 6 4 10z"/></svg></div>
  <h3>Quisquam</h3>
  <p>It is a long established fact that a reader will be distracted by the readable</p>
  <div class="more">Learn More →</div>
</div>
<div class="svc abs" style="left:434px">
  <div class="ring"><svg width="42" height="38" viewBox="0 0 42 38"><rect x="14" y="2" width="14" height="8" rx="2" fill="none" stroke="#fff" stroke-width="3"/><rect x="2" y="9" width="38" height="27" rx="4" fill="#fff"/><path d="M18 15h6v5h5v6h-5v5h-6v-5h-5v-6h5z" fill="#1a9bd8"/></svg></div>
  <h3>Dolorem</h3>
  <p>It is a long established fact that a reader will be distracted by the readable</p>
  <div class="more">Learn More →</div>
</div>
<div class="svc abs" style="left:752px">
  <div class="ring"><svg width="42" height="40" viewBox="0 0 42 40" fill="#fff"><path d="M21 0 L42 10 H0 Z"/><rect x="2" y="12" width="38" height="3"/><rect x="5" y="17" width="5" height="15"/><rect x="14" y="17" width="5" height="15"/><rect x="23" y="17" width="5" height="15"/><rect x="32" y="17" width="5" height="15"/><rect x="0" y="34" width="42" height="5"/></svg></div>
  <h3>Porro quisquam</h3>
  <p>It is a long established fact that a reader will be distracted by the readable content</p>
  <div class="more">Learn More →</div>
</div>

<section class="whatwedo abs"></section>
<div class="portrait abs"><div role="img" aria-label="Portrait photo of a smiling female doctor in a white coat"></div></div>
<h2 class="heading abs" style="left:475px;top:1724px">What We Do</h2>
<p class="abs" style="left:475px;top:1772px;width:545px;text-align:justify;font-size:12.5px;line-height:22px">It is a long established fact that a reader will be distracted by the readable content of a page when looking at its layout. The point of using Lorem Ipsum is that it has a more-or-less normal distribution of letters, as opposed to using 'Content here, content here', making it look like readable English. Many desktop publishing packages and web page editors now use Lorem Ipsum as their default model text, and a search for 'lorem ipsum' will uncover many web sites still in their infancy.</p>
<span class="btn abs" style="left:475px;top:1940px">Read More</span>

<section class="expect">
  <h2 class="heading abs">What We Expect</h2>
  <div class="faq abs" style="left:91px"><div class="q"><span>Q : Neque porro quisquam est dolorem ?</span><svg width="13" height="13" viewBox="0 0 13 13"><circle cx="6.5" cy="6.5" r="6.5" fill="#fff"/><rect x="3" y="5.5" width="7" height="2" fill="#0592cd"/></svg></div><div class="a"><b>A :</b> It is a long established fact that a reader will be distracted by the readable content of a page when looking at its layout.</div></div>
  <div class="faq abs" style="left:434px"><div class="q"><span>Q : Dolorem ipsum quia dolor sit amet?</span><svg width="13" height="13" viewBox="0 0 13 13"><circle cx="6.5" cy="6.5" r="6.5" fill="#fff"/><rect x="3" y="5.5" width="7" height="2" fill="#0592cd"/></svg></div><div class="a"><b>A :</b> It is a long established fact that a reader will be distracted by the readable content of a page when looking at its layout.</div></div>
  <div class="faq abs" style="left:778px"><div class="q"><span>Q : Porro quisquam est qui dolorem ?</span><svg width="13" height="13" viewBox="0 0 13 13"><circle cx="6.5" cy="6.5" r="6.5" fill="#fff"/><rect x="3" y="5.5" width="7" height="2" fill="#0592cd"/></svg></div><div class="a"><b>A :</b> It is a long established fact that a reader will be distracted by the readable content of a page when looking at its layout.</div></div>
</section>

<section class="testimonial abs" role="img" aria-label="Green-tinted background photo of a woman stretching outdoors"></section>
<h2 class="heading abs" style="left:0;top:2588px;width:1200px;text-align:center;color:#fff">Testimonial</h2>
<div class="quote abs">❝ It is a long established fact that a reader will be distracted by the readable content of a page when looking at its layout. The point of using Lorem Ipsum is that it has a more-or-less normal distribution of letters, as opposed to using 'Content here, content here', making it look like readable English ❞</div>
<svg class="abs" style="left:508px;top:2772px" width="16" height="26" viewBox="0 0 16 26"><path d="M13 2 L3 13 L13 24" fill="none" stroke="#fff" stroke-width="2.5"/></svg>
<div class="avatar abs" role="img" aria-label="Client portrait photo"></div>
<svg class="abs" style="left:670px;top:2772px" width="16" height="26" viewBox="0 0 16 26"><path d="M3 2 L13 13 L3 24" fill="none" stroke="#fff" stroke-width="2.5"/></svg>
<div class="person abs">Nora Hallevik</div>

<section class="blog">
  <h2 class="heading abs">Latest Blog</h2>
  <article class="post abs" style="left:109px"><div class="img" style="background:linear-gradient(#8fb7d6,#a7b38f 60%,#6f8a4f)" role="img" aria-label="Photo of a woman jogging on a mountain trail"><span class="date">14th May 2017</span></div><h4>NEQUE PORRO QUISQUAM</h4><p>It has survived not only five centuries, but also the leap into electronic typesetting, remaining</p><div class="more">Read More »</div></article>
  <article class="post abs" style="left:447px"><div class="img" style="background:linear-gradient(#4aa6e2,#9fd0f0)" role="img" aria-label="Photo of a woman raising her arms under a blue sky"><span class="date">14th May 2017</span></div><h4>NEQUE PORRO QUISQUAM</h4><p>It has survived not only five centuries, but also the leap into electronic typesetting, remaining</p><div class="more">Read More »</div></article>
  <article class="post abs" style="left:786px"><div class="img" style="background:linear-gradient(#d7e6ee,#b9c9a8)" role="img" aria-label="Photo of a smiling senior couple outdoors"><span class="date">14th May 2017</span></div><h4>NEQUE PORRO QUISQUAM</h4><p>It has survived not only five centuries, but also the leap into electronic typesetting, remaining</p><div class="more">Read More »</div></article>
</section>

<footer class="site-footer abs"></footer>
<div class="brand brand-foot abs"><span class="dot"></span><span>Meadow Medical Clinic</span></div>
<div class="fcol abs" style="left:417px;top:3536px">
  <h5>CONTACT US</h5>
  <ul class="contact-list">
    <li><svg width="10" height="14" viewBox="0 0 10 14"><path d="M5 0a5 5 0 0 1 5 5c0 4-5 9-5 9S0 9 0 5a5 5 0 0 1 5-5z" fill="#ddd"/><circle cx="5" cy="5" r="2" fill="#1f1f1f"/></svg><span>1280 Alder Lane<br>Brookfield Valley 40512</span></li>
    <li><svg width="12" height="12" viewBox="0 0 12 12"><path d="M2 0h3l1 3-2 1c1 2 2 3 4 4l1-2 3 1v3c0 1-1 2-2 2C5 12 0 7 0 2 0 1 1 0 2 0z" fill="#ddd"/></svg><span>555-019-4470</span></li>
    <li><svg width="12" height="10" viewBox="0 0 12 10"><rect width="12" height="10" fill="#ddd"/><path d="M0 0l6 5 6-5" fill="none" stroke="#1f1f1f"/></svg><span>hello@meadowclinic.example</span></li>
  </ul>
</div>
<div class="fcol abs" style="left:648px;top:3536px">
  <h5>JOIN OUR MAILING LIST</h5>
  <p class="note">Your about us information would fit here nicely.</p>
  <div class="mail-form"><span class="field">Email address</span><span class="go">Submit</span></div>
</div>
<div class="fcol abs" style="left:952px;top:3536px">
  <h5>FOLLOW US OUT THERE</h5>
  <div class="social"><span></span><span></span><span></span><span></span></div>
</div>
<div class="divider abs"></div>
<div class="copy abs">Copyright © 2017 All Rights Reserved</div>

</body>
</html>
```